business card for a massage therapy practice named 'Cedar and Willow Massage Studio'

I really need a trendy, yet easy on the eyes business card to complement my logo. Ideally with some gold or rose gold foil work.

My uploaded file of the logo I have in horizontal but I have a vertical version as well. Another color that is used in the website is a blush pink here and there. I'd like to see some trendy tropical leaves in the design.

```html
<!DOCTYPE html>
<html lang="en">
<head>
<meta charset="utf-8">
<title>Cedar and Willow Massage Studio — Business Card</title>
<link rel="stylesheet" href="https://fonts.googleapis.com/css2?family=Work+Sans:wght@400;600&display=swap">
<style>
  :root {
    --backdrop: #e6e6e3;
    --paper: #fbfbf9;
    --gold: #b8942f;
    --gold-soft: #c9a94a;
    --edge: #c9a227;
  }
  * { margin: 0; padding: 0; box-sizing: border-box; }
  html, body { width: 1200px; height: 800px; overflow: hidden; }
  body {
    background: var(--backdrop);
    font-family: "Work Sans", sans-serif;
    color: var(--gold);
    position: relative;
  }
  .card {
    position: absolute;
    top: 257px;
    width: 500px;
    height: 286px;
    background: var(--paper);
    border: 2px solid var(--edge);
    box-shadow: 0 6px 18px rgba(0, 0, 0, 0.12);
  }
  .card--front { left: 70px; }
  .card--back { left: 630px; }

  /* Front: brand name */
  .brand {
    position: absolute;
    left: 0; right: 0; top: 0; bottom: 0;
    display: flex;
    align-items: center;
    justify-content: center;
    gap: 16px;
  }
  .brand__dot {
    width: 18px; height: 18px;
    border-radius: 50%;
    background: var(--gold);
  }
  .brand__name {
    font-weight: 600;
    font-size: 24px;
    line-height: 1.25;
    letter-spacing: 0.06em;
    text-transform: uppercase;
    color: var(--gold);
  }

  /* Back: person and contact */
  .identity {
    position: absolute;
    left: 30px;
    top: 138px;
    width: 190px;
    text-align: right;
  }
  .identity__name {
    font-weight: 600;
    font-size: 20px;
    letter-spacing: 0.08em;
    text-transform: uppercase;
  }
  .identity__role {
    font-weight: 400;
    font-size: 13px;
    letter-spacing: 0.03em;
    margin-top: 2px;
  }
  .divider {
    position: absolute;
    left: 236px;
    top: 104px;
    width: 1px;
    height: 84px;
    background: var(--gold-soft);
  }
  .contact {
    position: absolute;
    left: 252px;
    top: 110px;
    list-style: none;
  }
  .contact__item {
    display: flex;
    align-items: center;
    gap: 9px;
    font-size: 13px;
    letter-spacing: 0.02em;
    height: 24px;
  }
  .contact__icon { width: 12px; height: 12px; flex: none; }
</style>
</head>
<body>
  <section class="card card--front">
    <div class="brand">
      <span class="brand__dot"></span>
      <p class="brand__name">Cedar and Willow<br>Massage Studio</p>
    </div>
  </section>

  <section class="card card--back">
    <div class="identity">
      <p class="identity__name">Owen Hartley</p>
      <p class="identity__role">Design Consultant</p>
    </div>
    <div class="divider"></div>
    <ul class="contact">
      <li class="contact__item">
        <svg class="contact__icon" viewBox="0 0 12 12" fill="none" stroke="currentColor" stroke-width="1.2">
          <rect x="3" y="0.8" width="6" height="10.4" rx="1"/>
          <line x1="5" y1="9.4" x2="7" y2="9.4"/>
        </svg>
        <span>555-214-0386</span>
      </li>
      <li class="contact__item">
        <svg class="contact__icon" viewBox="0 0 12 12" fill="none" stroke="currentColor" stroke-width="1.2">
          <rect x="0.8" y="2.4" width="10.4" height="7.2"/>
          <polyline points="0.8,2.4 6,6.6 11.2,2.4"/>
        </svg>
        <span>info@cedarwillow.com</span>
      </li>
      <li class="contact__item">
        <svg class="contact__icon" viewBox="0 0 12 12" fill="none" stroke="currentColor" stroke-width="1.1">
          <circle cx="6" cy="6" r="5.2"/>
          <ellipse cx="6" cy="6" rx="2.3" ry="5.2"/>
          <line x1="0.8" y1="6" x2="11.2" y2="6"/>
        </svg>
        <span>www.cedarwillow.com</span>
      </li>
    </ul>
  </section>
</body>
</html>
```